Banner to be displayed at local Farmers Market Booth.

Graphic Design Brief: Farmers Market Banner Contest

Project Overview:We are seeking talented graphic designers to create a visually appealing banner for our booth at the local farmers market. Our company specializes in healthy, all-natural dog and cat treats, and we want a banner that captures our brand identity while drawing in pet owners who value quality and nutrition for their furry friends.

Banner Specifications:

Size: 24 inches x 60 inches (Horizontal orientation) 24" High X 60 wide

Theme: Vintage/Retro

Style: Warm, inviting, nostalgic with a touch of rustic charm

Colors: Earthy, muted tones such as warm browns, soft greens, and creamy yellows. Pops of red or blue may be used sparingly for accents. OR Black and White with gray scales. Would like to see both

Typography: Retro-style fonts that are readable and align with the vintage aesthetic.

Key Elements to Include: website (www.moltbyfarms.com)

Company Name: Moltby Farms

Tagline: " Simply Honest Bites "
Imagery: Illustrations or stylized graphics of happy dogs and cats, possibly interacting with treats.

Emphasis on Natural Ingredients: Icons or design elements that subtly suggest freshness and quality (e.g., leaves, wheat, bones, or paw prints).

Farmers Market Appeal: A design that blends well with the artisanal, handmade, and farm-fresh atmosphere of the market.

Design Considerations:

The banner should be easily readable from a distance.

A balanced composition that doesn't feel overcrowded.

Should evoke trust and warmth while maintaining a professional look.

Avoid overly modern or sleek elements that don’t align with the vintage aesthetic.

Submission Requirements:

High-resolution digital file in PDF or AI format.

CMYK color mode for printing purposes.

Must include a mockup or preview of how it would look in a real farmers market setting.

We look forward to seeing your creative interpretations of our brand! If you have any questions, feel free to reach out.

Font styles to use
Other font styles liked:
• See attachement

Requirements
Nice to have
• Retro/Vintage,playful BUT NOT whimsical

```html
<!DOCTYPE html>
<html lang="en">
<head>
<meta charset="utf-8">
<title>Moltby Farms – Market Banner</title>
<link rel="stylesheet" href="https://fonts.googleapis.com/css2?family=Kanit:wght@500;600&family=Playfair+Display:wght@900&display=swap">
<style>
  :root {
    --page-bg: #f1f1f1;
    --yellow: #f7d31c;
    --yellow-light: #fbe35c;
    --red: #d53b27;
    --red-light: #e86a3f;
    --blue: #22397a;
    --border-red: #cf3126;
    --ink: #161616;
    --white: #ffffff;
    --art-warm: #e9b46a;
    --art-cool: #cfcfd6;
  }
  * { margin: 0; padding: 0; box-sizing: border-box; }
  html, body { width: 1200px; height: 1200px; overflow: hidden; }
  body { background: var(--page-bg); position: relative; }

  .banner {
    position: absolute;
    left: 0; top: 360px;
    width: 1200px; height: 480px;
    overflow: hidden;
    background: repeating-linear-gradient(90deg, var(--yellow) 0 9px, var(--yellow-light) 9px 18px);
    box-shadow: 0 8px 24px rgba(0,0,0,0.18);
  }
  .banner__base-band {
    position: absolute;
    left: 0; right: 0; top: 369px; bottom: 0;
    background: repeating-linear-gradient(90deg, var(--red) 0 9px, var(--red-light) 9px 18px);
  }
  .banner__shape { position: absolute; inset: 0; }

  .brand-name {
    position: absolute;
    left: 40px; top: 90px;
    width: 220px;
    text-align: center;
    font-family: "Kanit", sans-serif;
    font-weight: 600;
    font-size: 34px;
    line-height: 1;
    color: var(--ink);
  }

  .tagline {
    position: absolute;
    left: 300px; top: 78px;
    width: 600px;
    text-align: center;
    font-family: "Playfair Display", serif;
    font-weight: 900;
    font-size: 58px;
    line-height: 0.98;
    color: var(--white);
    text-transform: uppercase;
  }

  .web-pill {
    position: absolute;
    left: 402px; top: 225px;
    width: 396px; height: 48px;
    border-radius: 24px;
    background: var(--border-red);
    color: var(--white);
    font-family: "Kanit", sans-serif;
    font-weight: 500;
    font-size: 27px;
    letter-spacing: 0.5px;
    display: flex; align-items: center; justify-content: center;
  }

  .pet-lineup {
    position: absolute;
    left: 264px; top: 282px;
    width: 672px; height: 198px;
    border-radius: 90px 90px 0 0;
    background: linear-gradient(90deg, var(--art-warm), var(--art-cool) 35%, var(--art-warm) 65%, var(--art-cool));
  }
</style>
</head>
<body>
  <section class="banner">
    <div class="banner__base-band"></div>

    <svg class="banner__shape" viewBox="0 0 1200 480" width="1200" height="480" aria-hidden="true">
      <path class="panel-border" fill="var(--border-red)"
        d="M238 480 L238 250 C238 180 280 130 375 124 C385 70 450 32 600 30 C750 32 815 70 825 124 C920 130 962 180 962 250 L962 480 Z"/>
      <path class="panel-fill" fill="var(--blue)"
        d="M252 480 L252 252 C252 190 290 146 386 140 C396 88 455 46 600 44 C745 46 804 88 814 140 C910 146 948 190 948 252 L948 480 Z"/>
    </svg>

    <div class="brand-name">Moltby Farms</div>

    <h1 class="tagline">Simply<br>Honest Bites</h1>

    <div class="web-pill">www.moltbyfarms.com</div>

    <div class="pet-lineup" role="img" aria-label="Illustrated line-up of happy dogs, cats and a small bird sitting together"></div>
  </section>
</body>
</html>
```